PIPE RELINING COMPANY NEEDS A NEW INFORMATIVE FLYER CREATED

We are a company that sells a service to residential homeowners (using a particular state of the art international product) and we need to refresh our A4 tri- fold flyer (z fold 6 pages). The layout needs to include pictures, heading and text boxes, but be simple and clean cut at the same time.

The front of the flyer must have the attached picture of the pipe under the house, logo and website.

This flyer is going to be given to clients and to leave with them when we quote for work.

Our colour scheme is black, white, red. A highlight colour if needed (in small amounts) could be 100% cyan and also a bright orange.

I have attached the copy of the text and this can be spread out throughout the brochure.

We are a professional and industry leading company so it needs to be professional, clean cut but with a modern edge.

Target Market(s)

HOMEOWNERS

Industry/Entity Type

It Company

Font styles to use
Sans Serif

Colors
ec1f27
ffffff
000000
f37122

Requirements
Must have
• PROFESSINAL, MODERN
• USE OF BLACK, RED AND WHITE - REFER LOGO
Should not have
• BE CLUTTERED

```html
<!DOCTYPE html>
<html lang="en">
<head>
<meta charset="utf-8">
<title>Pipecore Trifold Brochure – Inside</title>
<link href="https://fonts.googleapis.com/css2?family=Lato:ital,wght@0,300;0,400;0,700;0,900;1,300;1,400;1,700;1,900&display=swap" rel="stylesheet">
<style>
:root{
  --red:#ec1f27;
  --orange:#f37122;
  --cyan:#1a9ad6;
  --black:#000000;
  --white:#ffffff;
  --ink:#333333;
  --grey:#555555;
  --stage:#bdbec0;
  --title-grey:#6d6e70;
  --gold:#ecc243;
}
*{margin:0;padding:0;box-sizing:border-box}
html,body{width:1200px;height:980px;overflow:hidden}
body{background:var(--stage);font-family:'Lato',sans-serif;position:relative;color:var(--ink)}
.abs{position:absolute}
.board-title{left:37px;top:34px;font-weight:900;font-size:26px;color:var(--title-grey);letter-spacing:.2px}
.sheet{left:45px;top:73px;width:1114px;height:866px;background:var(--white)}
.h-section{color:var(--red);font-weight:900;font-style:italic;font-size:27px;line-height:25px;letter-spacing:-.3px}
.sub-orange{color:var(--orange);font-weight:700;font-size:12.4px;line-height:15px;text-transform:uppercase}
.body{font-size:12px;line-height:15px;color:var(--ink)}
.why{left:79px;top:103px;width:310px}
.why .h-section{margin-bottom:26px}
.why .sub-orange{margin-bottom:8px}
.why .body{margin-bottom:9px}
.warranty-text{width:230px}
.seal{left:325px;top:532px;width:74px;height:74px;border-radius:50%;background:var(--gold)}
.photo{height:137px}
.photo-label{background:var(--red);color:var(--white);font-size:15.5px;height:29px;line-height:29px;padding-left:22px}
.photo-1{left:416px;top:90px;width:193px}
.photo-2{left:617px;top:90px;width:171px}
.photo-2 .photo-label{padding-left:5px}
.meaning{left:452px;top:282px;width:330px}
.meaning ul{list-style:none;margin-top:24px;padding-left:26px}
.meaning li{font-size:12.4px;line-height:18px;color:var(--grey);position:relative}
.meaning li::before{content:"";position:absolute;left:-17px;top:7px;width:5px;height:5px;border-radius:50%;background:var(--red)}
.call{left:452px;top:560px;font-style:italic;font-weight:300;font-size:23px;line-height:27px;color:var(--red)}
.call span{display:block;color:var(--black);padding-left:23px}
.know{left:822px;top:103px;width:306px}
.know .h-section{margin-bottom:26px}
.know h3{color:var(--cyan);font-weight:700;font-size:12.3px;line-height:15px}
.know .body{margin-bottom:14px}
.web{left:848px;top:594px}
.band{left:45px;top:650px;width:1114px;height:289px;background:#0b0b0b}
.tab-patch{left:81px;top:637px}
.tab-result{left:812px;top:685px}
.step-img{border:2px solid var(--red);width:106px;height:74px}
.num{width:33px;height:33px;border-radius:50%;background:var(--white);border:2px solid var(--red);color:var(--red);font-size:25px;line-height:28px;text-align:center;font-weight:400}
.cap{color:var(--white);font-size:10.3px;line-height:14px}
.tagline{left:1001px;top:795px;width:135px;color:var(--red);font-style:italic;font-size:21px;line-height:20.5px;letter-spacing:-.3px}
</style>
</head>
<body>
<div class="abs board-title">TRIFOLD BROCHURE INSIDE</div>
<div class="abs sheet"></div>

<section class="abs why">
  <h2 class="h-section">WHY IT WORKS</h2>
  <p class="sub-orange">Pipecore uses epoxy rein not polyester or silicate resins.</p>
  <p class="body">Why? Because epoxy resin does not shrink. Polyester and silicate resins can shrink in the pipe allowing tree roots to return.</p>
  <p class="sub-orange">Pipecore inverts th eliner instead of using a drag-in method.</p>
  <p class="body">Why? Because this means that the resin has contact with the host pipe impregnating the cracks and joins the pipework. With the drag in method, the resin does not have contact with the host pipe and cannot impregnate the cracks and joins.</p>
  <p class="sub-orange">Pipecore uses a German system called Flexaliner.</p>
  <p class="body">Why? Because it has been extensively tested in Europe and came out as the test winner in standard and extreme conditions based on all assessment criteria – effective-ness, density and load carrying capacity. Flexaliner has a proven track record and bee used to reline hundreds of kms throughout Europe.</p>
  <p class="sub-orange">Pipecore provides a 25 year warranty</p>
  <p class="body warranty-text">Why?&nbsp; Because we understand the quality of the equipment and product and how we install it. We were one of the first to reline in NSW and are constantly carrying out research and development.</p>
</section>
<div class="abs seal" role="img" aria-label="25 year product warranty seal"></div>

<div class="abs photo-1">
  <div class="photo" role="img" aria-label="Photo of a cracked old pipe buried in soil" style="background:linear-gradient(180deg,#5a4032 0%,#8a7a6c 45%,#5a3b2c 70%,#3e281e 100%)"></div>
  <div class="photo-label">Common Pipe Issues</div>
</div>
<div class="abs photo-2">
  <div class="photo" role="img" aria-label="Photo of a green liner inside an old pipe" style="background:linear-gradient(90deg,#48b418 0%,#8ee84c 50%,#47b01a 100%)"></div>
  <div class="photo-label">Pipe inside the old Pipe</div>
</div>

<section class="abs meaning">
  <h2 class="h-section">WHAT DOES PIPE<br>RELINING MEAN?</h2>
  <ul>
    <li>Permanent jointless liner</li>
    <li>50 years life expectancy</li>
    <li>Up front price</li>
    <li>Environmentally sound</li>
    <li>Eliminates structural disturbances</li>
    <li>Imprevious to future root penetration</li>
    <li>Provides increased flow characteristics</li>
    <li>Suitable for industrial, residential and commercial applications</li>
  </ul>
</section>
<p class="abs call">Call For Free Expert Advice<span>&amp; Great Rates On Pipe Relining</span></p>

<section class="abs know">
  <h2 class="h-section">THINGS YOUR SHOULD<br>KNOW</h2>
  <h3>Knowledge &amp; Experience</h3>
  <p class="body">We train other plumbers and have been doing it for over 10 years.</p>
  <h3>We're An Owned &amp; Operated Business</h3>
  <p class="body">We take great pride in our work. Our business is based on relationships not transactions.</p>
  <h3>We Use the best in class pipe relining solution</h3>
  <p class="body">We have sourced the best products and equipment from around the world and our Relinex product is from Germany.</p>
  <h3>We have state of the art equipment.</h3>
  <p class="body">Our truck is customer designed and filly equipped with latest technology to carry out pipe relining.</p>
  <h3>We're Fully licensed &amp; Insured</h3>
  <p class="body">All of our technicians are fully licensed and qualified to complete the job. Our company is fully insured and are happy to provide you with documentation.</p>
  <h3>After Sales Service</h3>
  <p class="body">We don't forget about you after the job and as part of the warranty we carry out an annual camera inspection of the drainage.</p>
</section>
<svg class="abs web" width="258" height="33" viewBox="0 0 258 33">
  <polygon points="22,0 258,0 236,33 0,33" fill="var(--red)"/>
  <text x="127" y="21.5" text-anchor="middle" fill="#fff" font-family="Lato,sans-serif" font-size="13" letter-spacing="3.2" font-style="italic">www.nodigpipes.com.au</text>
</svg>

<div class="abs band"></div>
<svg class="abs tab-patch" width="220" height="40" viewBox="0 0 220 40">
  <polygon points="20,0 220,0 200,40 0,40" fill="var(--red)"/>
  <text x="26" y="27" fill="#fff" font-family="Lato,sans-serif" font-size="19" font-style="italic" font-weight="300">Patch Repair Process</text>
</svg>

<div class="abs step-img" style="left:89px;top:716px" role="img" aria-label="Photo of a technician beside the service truck"><div style="width:100%;height:100%;background:linear-gradient(135deg,#3a3a3a,#7a6c66 60%,#2a2a2a)"></div></div>
<div class="abs num" style="left:102px;top:702px">1</div>
<p class="abs cap" style="left:90px;top:807px;width:125px">Clean the line with a high pressure water jetter, and carry out a camera inspection to determine the exact location and cause of the problems.</p>

<div class="abs step-img" style="left:249px;top:723px" role="img" aria-label="Photo of a liner being prepared in a workshop"><div style="width:100%;height:100%;background:linear-gradient(135deg,#d8d8d8,#9a9a9a 55%,#3a8a4a)"></div></div>
<div class="abs num" style="left:262px;top:702px">2</div>
<p class="abs cap" style="left:250px;top:808px;width:125px">Prepare the liner. Cut the liner to the correct length, mix the appropri-ate amount of rein and impregnate the rein into the liner.</p>

<div class="abs step-img" style="left:455px;top:716px" role="img" aria-label="Photo of workers inverting the liner with equipment"><div style="width:100%;height:100%;background:linear-gradient(135deg,#6a6a6a,#b0b0b0 50%,#4a4a4a)"></div></div>
<div class="abs num" style="left:466px;top:702px">3</div>
<p class="abs cap" style="left:456px;top:802px;width:110px">Invert the liner into the pipe, inflate and then cure.</p>

<div class="abs step-img" style="left:587px;top:723px" role="img" aria-label="Photo of technicians working at a drain access point"><div style="width:100%;height:100%;background:linear-gradient(135deg,#5a5a52,#9ea08e 55%,#3a3a34)"></div></div>
<div class="abs num" style="left:599px;top:702px">4</div>
<p class="abs cap" style="left:589px;top:808px;width:150px">A seamless, flexible liner is cut to length and filled with environmentally safe epoxy rein. The liner is them inverted into the existing, host pipe and inflated using compressed air. Once the liner is fully cured with hot water, it is ready for use.</p>

<svg class="abs tab-result" width="124" height="34" viewBox="0 0 124 34">
  <polygon points="18,0 124,0 106,34 0,34" fill="var(--red)"/>
  <text x="30" y="24" fill="#fff" font-family="Lato,sans-serif" font-size="18" font-style="italic" font-weight="300">RESULT</text>
</svg>
<p class="abs cap" style="left:842px;top:750px;width:128px">The result is a completely new pipe inside the old. This pipe within a pie is 100% water tight, stronger than PVC pipe, and has an increased flow rate compared to most existing pipes. Relined pipes have a life expectancy of 50 years and our installation work has a 25 year guarantee.</p>

<div class="abs step-img" style="left:980px;top:693px;width:132px;height:92px" role="img" aria-label="Photo of a relined green pipe among tree roots"><div style="width:100%;height:100%;background:linear-gradient(135deg,#6a5240,#a08a70 40%,#3aa23a 70%,#5a4030)"></div></div>
<div class="abs num" style="left:1061px;top:676px;width:36px;height:36px;font-size:28px;line-height:31px">5</div>
<p class="abs tagline">A fast, clean, permanent solution for fixing blocked drains.</p>
</body>
</html>
```